Brightmill Data Works

Our company is about IT hardwares and IT solutions. IT hardware such as PC, RAMS, storage and servers. IT solutions such as project management, BA. We are also selling new technology too.

Target Market(s)

Consumer, Small to Medium Business, Corporate

Requirements
Must have
• The business card must have the following:
• Name:
• Title:
• Contact Number:
• Email address:
• Website:
• Color: Must match the logo color upgrade

```html
<!DOCTYPE html>
<html lang="en">
<head>
<meta charset="UTF-8">
<title>Brightmill Data Works — Business Card</title>
<link href="https://fonts.googleapis.com/css2?family=Work+Sans:wght@400;500;700&display=swap" rel="stylesheet">
<style>
  :root {
    --backdrop: #1a1a1a;
    --card: #232323;
    --card-edge: #2c2c2c;
    --silver: #b9b9b9;
    --white: #f4f4f4;
    --amber: #e79a34;
    --muted: #d9d9d9;
  }
  * { margin: 0; padding: 0; box-sizing: border-box; }
  html, body {
    width: 1200px;
    height: 900px;
    overflow: hidden;
    background: var(--backdrop);
    font-family: "Work Sans", sans-serif;
  }
  .stage {
    position: relative;
    width: 1200px;
    height: 900px;
  }
  .card {
    position: absolute;
    left: 270px;
    width: 660px;
    height: 377px;
    background: var(--card);
    border: 1px solid var(--card-edge);
  }
  .card--front { top: 50px; }
  .card--back  { top: 473px; }

  /* Front */
  .front-brand {
    position: absolute;
    inset: 0;
    display: flex;
    flex-direction: column;
    align-items: center;
    justify-content: center;
    gap: 22px;
  }
  .brand-dot {
    width: 44px;
    height: 44px;
    border-radius: 50%;
    background: var(--silver);
  }
  .front-brand .brand-name {
    font-weight: 700;
    font-size: 40px;
    letter-spacing: 1px;
    text-transform: uppercase;
    color: var(--silver);
  }

  /* Back */
  .back-brand {
    position: absolute;
    left: 0;
    top: 0;
    width: 340px;
    height: 100%;
    display: flex;
    flex-direction: column;
    align-items: center;
    justify-content: center;
    gap: 20px;
  }
  .back-brand .brand-dot { background: var(--amber); width: 40px; height: 40px; }
  .back-brand .brand-name {
    font-weight: 700;
    font-size: 30px;
    line-height: 1.15;
    text-transform: uppercase;
    text-align: center;
    color: var(--white);
  }
  .divider {
    position: absolute;
    left: 352px;
    top: 92px;
    width: 2px;
    height: 194px;
    background: var(--white);
  }
  .contact {
    position: absolute;
    left: 384px;
    top: 92px;
    width: 260px;
    color: var(--white);
  }
  .contact__name {
    font-size: 25px;
    font-weight: 500;
    text-transform: uppercase;
    color: var(--amber);
    line-height: 1.05;
  }
  .contact__title {
    font-size: 16px;
    margin-bottom: 18px;
  }
  .contact__address {
    font-size: 15px;
    line-height: 1.35;
    margin-bottom: 14px;
  }
  .contact__row {
    display: flex;
    align-items: center;
    gap: 10px;
    font-size: 15px;
    line-height: 1.5;
  }
  .contact__row svg { width: 13px; height: 13px; flex: none; }
  .accent { color: var(--amber); }
</style>
</head>
<body>
<main class="stage">
  <section class="card card--front">
    <div class="front-brand">
      <span class="brand-dot"></span>
      <span class="brand-name">Brightmill Data Works</span>
    </div>
  </section>

  <section class="card card--back">
    <div class="back-brand">
      <span class="brand-dot"></span>
      <span class="brand-name">Brightmill<br>Data Works</span>
    </div>
    <div class="divider"></div>
    <div class="contact">
      <p class="contact__name">Dana Whitford</p>
      <p class="contact__title">Director</p>
      <p class="contact__address">2250 Orchard Vale Ave<br>Fernbrook, CA 95012-4480</p>
      <p class="contact__row">
        <svg viewBox="0 0 16 16" aria-hidden="true"><path d="M4 1 L6.5 4 L5 6 Q7 10 10 11 L12 9.5 L15 12 L13 15 Q4 14 1 4 Z" fill="none" stroke="#e79a34" stroke-width="1.5" stroke-linejoin="round"/></svg>
        555-214-7730
      </p>
      <p class="contact__row">
        <svg viewBox="0 0 16 16" aria-hidden="true"><rect x="1" y="3" width="14" height="10" fill="none" stroke="#e79a34" stroke-width="1.5"/><path d="M1 3 L8 9 L15 3" fill="none" stroke="#e79a34" stroke-width="1.5"/></svg>
        hello@brightmilldata.com
      </p>
      <p class="contact__row">
        <svg viewBox="0 0 16 16" aria-hidden="true"><circle cx="8" cy="8" r="6.5" fill="none" stroke="#e79a34" stroke-width="1.4"/><ellipse cx="8" cy="8" rx="3" ry="6.5" fill="none" stroke="#e79a34" stroke-width="1.2"/><path d="M1.5 8 H14.5" stroke="#e79a34" stroke-width="1.2"/></svg>
        <span>www.<span class="accent">brightmilldata</span>.com</span>
      </p>
    </div>
  </section>
</main>
</body>
</html>
```